Logo Tweaks & Stationery Design Project for Energy Management Co

We are a specialist metering company trading for over 60 years and have recently developed GPRS metering infrastructure & monitoring services. For more information please see http://www.kestrel-vale.example/remote-meter-reading.html

Due to the success of this system it’s become necessary to open a new company “Brightwell Gauge Ltd” and this project is for relevant stationary designs for our documents.

I need something modern and clear to match our new logo style. Feel free to play around with the colors and tweak the logo if you like.

Maybe with some line chart animation on the header relating to our online services. ( See inspiration file )

Thanks
Derek

Target Market(s)

Renewable Energy Generation Monitoring, Energy Management, Remote Monitoring and Tennant Billing.

Industry/Entity Type

It Company

Requirements
Nice to have
• 100% Carbon neutral hosting
Should not have
• "Clip-Art" should not be used.

```html
<!DOCTYPE html>
<html lang="en">
<head>
<meta charset="utf-8">
<title>Brightwell Gauge Ltd – Envelope</title>
<link rel="stylesheet" href="https://fonts.googleapis.com/css2?family=Orbitron:wght@500;700&family=Tinos&display=swap">
<style>
  :root {
    --page-bg: #e9e4da;
    --paper: #ffffff;
    --edge: #3a3a3a;
    --brand-blue: #233a96;
    --brand-red: #be1e2d;
    --wordmark-blue: #3a2fb0;
    --strip-grey: #6b6b6e;
    --label-ink: #111111;
  }
  html, body {
    margin: 0;
    padding: 0;
    width: 960px;
    height: 1200px;
    overflow: hidden;
    background: var(--page-bg);
  }
  .sheet { display: block; width: 960px; height: 1200px; }
  .view-label { font-family: "Tinos", serif; font-size: 42px; fill: var(--label-ink); }
  .paper { fill: var(--paper); stroke: var(--edge); stroke-width: 1; }
  .fold-line { fill: none; stroke: var(--edge); stroke-width: 1; }
  .front-band { fill: var(--brand-red); }
  .corner-arc { fill: var(--brand-red); }
  .corner-disc { fill: var(--brand-blue); }
  .back-flap { fill: var(--brand-blue); }
  .back-strip { fill: var(--strip-grey); }
  .front-wordmark {
    font-family: "Orbitron", sans-serif;
    font-weight: 700;
    font-size: 34px;
    fill: var(--wordmark-blue);
  }
  .back-wordmark {
    font-family: "Orbitron", sans-serif;
    font-weight: 700;
    font-size: 22px;
    letter-spacing: 2px;
    fill: var(--brand-blue);
  }
</style>
</head>
<body>
<svg class="sheet" viewBox="0 0 960 1200" xmlns="http://www.w3.org/2000/svg">
  <text class="view-label" x="10" y="60">Envelop</text>

  <g class="envelope envelope--front">
    <path class="paper" d="M168 183 L197 123 L527 60 L820 123 L854 183 Z"/>
    <rect class="paper" x="168" y="183" width="686" height="320"/>
    <rect class="front-band" x="168" y="433" width="600" height="70"/>
    <path class="corner-arc" d="M694 503 C694 400 760 334 854 331 V503 Z"/>
    <path class="corner-disc" d="M712 503 C714 412 772 352 854 347 V503 Z"/>
    <text class="front-wordmark" x="196" y="482">Brightwell Gauge</text>
  </g>

  <text class="view-label" x="172" y="572">Front</text>

  <g class="envelope envelope--back">
    <rect class="paper" x="153" y="698" width="687" height="319"/>
    <path class="back-flap" d="M153 698 L183 637 L513 574 L806 637 L840 698 Z"/>
    <path class="fold-line" d="M153 698 L476 767 L840 698"/>
    <rect class="back-strip" x="153" y="981" width="687" height="36"/>
    <text class="back-wordmark" x="480" y="1008" text-anchor="middle">BRIGHTWELL GAUGE</text>
  </g>

  <text class="view-label" x="172" y="1068">Back</text>
</svg>
</body>
</html>
```